Carpet cleaning company focused on high quality needs business cards

We are a growing company that just merged with another company and need to design a new business card. We do both residential as well as commercial cleaning. We do carpet, tile & grout, upholstery, hard floors, and stain & pet odor removal. We treat our customers like family and strive to achieve outstanding results with every job.

```html
<!DOCTYPE html>
<html lang="en">
<head>
<meta charset="utf-8">
<title>Pal's Fresh Crew Cleaning – Business Card</title>
<link href="https://fonts.googleapis.com/css2?family=Lato:wght@400;700;900&display=swap" rel="stylesheet">
<style>
  :root {
    --backdrop: #2a2a2a;
    --card: #e4e4e4;
    --card-light: #efefef;
    --ink: #1c1c1c;
    --brand-red: #e3413b;
    --name-red: #d8403a;
    --title-gold: #a98a4e;
    --text-grey: #3a3a3a;
    --icon-blue: #1b78b8;
    --rule: #555555;
    --art-fill: #d2d2d2;
  }
  * { margin: 0; padding: 0; box-sizing: border-box; }
  html, body { width: 1200px; height: 1200px; overflow: hidden; background: var(--backdrop); }
  body { position: relative; font-family: "Lato", sans-serif; }

  .card {
    position: absolute;
    left: 201px;
    width: 797px;
    height: 455px;
    border-radius: 24px;
    overflow: hidden;
    background: linear-gradient(160deg, var(--card) 0%, var(--card-light) 100%);
  }
  .card--front { top: 96px; }
  .card--back { top: 656px; }

  /* Front */
  .brand-lockup {
    position: absolute;
    left: 73px;
    top: 190px;
    display: flex;
    align-items: center;
    gap: 18px;
  }
  .brand-lockup__mark { width: 72px; height: 72px; background: var(--brand-red); flex: none; }
  .brand-lockup__name {
    font-weight: 900;
    color: var(--ink);
    font-size: 25px;
    line-height: 1.08;
    text-transform: uppercase;
  }
  .divider {
    position: absolute;
    left: 429px;
    top: 118px;
    width: 1.5px;
    height: 210px;
    background: var(--rule);
  }
  .contact-block { position: absolute; left: 471px; top: 112px; }
  .contact-block__name {
    font-weight: 700;
    font-size: 36px;
    letter-spacing: 1px;
    color: var(--name-red);
    line-height: 1.1;
  }
  .contact-block__title {
    font-size: 21px;
    letter-spacing: 0.5px;
    color: var(--title-gold);
    margin-top: 2px;
  }
  .contact-list { list-style: none; margin-top: 14px; }
  .contact-list li {
    display: flex;
    align-items: flex-start;
    gap: 14px;
    font-size: 19px;
    letter-spacing: 0.3px;
    color: var(--text-grey);
    line-height: 26px;
  }
  .contact-list li.gap { margin-top: 8px; }
  .contact-list svg { width: 16px; height: 16px; margin-top: 5px; flex: none; fill: var(--icon-blue); }

  /* Back */
  .back-band { position: absolute; inset: 0; width: 797px; height: 455px; }
  .back-name {
    position: absolute;
    left: 71px;
    top: 66px;
    font-weight: 900;
    color: var(--ink);
    line-height: 1;
    text-transform: uppercase;
  }
  .back-name__lead { display: block; font-size: 92px; text-transform: none; letter-spacing: -1px; }
  .back-name__line { display: block; font-size: 46px; margin-top: 4px; letter-spacing: 0.3px; }
  .art-area {
    position: absolute;
    left: 447px;
    top: 10px;
    width: 305px;
    height: 430px;
    background: var(--art-fill);
  }
</style>
</head>
<body>

<section class="card card--front">
  <div class="brand-lockup">
    <span class="brand-lockup__mark"></span>
    <span class="brand-lockup__name">Pal's<br>Fresh Crew<br>Cleaning</span>
  </div>

  <div class="divider"></div>

  <div class="contact-block">
    <h1 class="contact-block__name">MARK ELLISON</h1>
    <p class="contact-block__title">Founder &amp; CEO</p>
    <ul class="contact-list">
      <li>
        <svg viewBox="0 0 16 16"><path d="M8 0a5.5 5.5 0 0 0-5.5 5.5C2.5 9.6 8 16 8 16s5.5-6.4 5.5-10.5A5.5 5.5 0 0 0 8 0zm0 8a2.5 2.5 0 1 1 0-5 2.5 2.5 0 0 1 0 5z"/></svg>
        <span>4178 Alder Lane<br>Norwalk, CT 06851</span>
      </li>
      <li class="gap">
        <svg viewBox="0 0 16 16"><path d="M3.6 1l2.3 2.6-1.3 2c.9 1.9 2.3 3.3 4.2 4.2l2-1.3L13.4 11l-1.6 2.7C6.2 13.4 2.6 9.8 2.3 4.2z"/></svg>
        <span>(203) 555-0147</span>
      </li>
      <li>
        <svg viewBox="0 0 16 16"><path d="M1 3.5h14v9H1zM2.2 4.5 8 9l5.8-4.5z" fill-rule="evenodd"/></svg>
        <span>hello@palsfreshcrew.com</span>
      </li>
      <li>
        <svg viewBox="0 0 16 16"><circle cx="8" cy="8" r="7"/><path d="M5 4.5c1.5.3 2 1.5 1 2.5s.5 2.5 1.5 3-1 3-1 3M10 3c-.5 1.5.5 2.5 2 2.5s1 3-.5 3.5" stroke="#e6e6e6" stroke-width="1.3" fill="none"/></svg>
        <span>palsfreshcrew.com</span>
      </li>
    </ul>
  </div>
</section>

<section class="card card--back">
  <svg class="back-band" viewBox="0 0 797 455" aria-hidden="true">
    <polygon points="0,455 797,220 797,455" fill="var(--brand-red)"/>
  </svg>
  <div class="back-name">
    <span class="back-name__lead">Pal's</span>
    <span class="back-name__line">Fresh Crew</span>
    <span class="back-name__line">Cleaning</span>
  </div>
  <div class="art-area" role="img" aria-label="Brand illustration area"></div>
</section>

</body>
</html>
```